need eczema bath soak label/bag

need you to recreate this please. ai file. recreate this exact image please. ...if you want a big tip, create some different styles.

Colors
0054AA
0677BA
7BADD7
CADEEF
E8F1F8

```html
<!DOCTYPE html>
<html lang="en">
<head>
<meta charset="utf-8">
<title>The Surf Soothed Soak – Bath Soak Label</title>
<link href="https://fonts.googleapis.com/css2?family=Montserrat:wght@300;400;600;800&display=swap" rel="stylesheet">
<style>
  :root {
    --ink: #0c1d30;
    --stage: #0b1a2a;
    --paper: #ffffff;
    --mist: #e8f1f8;
    --sky-wash: #cadeef;
    --wave-light: #7badd7;
    --wave: #0677ba;
    --wave-deep: #0054aa;
    --foam: #f3f5f6;
    --wet-sand: #d8d0c4;
    --sand: #dcb67d;
    --sand-light: #e8c994;
  }
  * { margin: 0; padding: 0; box-sizing: border-box; }
  html, body {
    width: 1200px;
    height: 888px;
    overflow: hidden;
    background: var(--stage);
    font-family: "Montserrat", sans-serif;
    color: var(--ink);
  }
  .label {
    position: absolute;
    left: 334px;
    top: 0;
    width: 533px;
    height: 888px;
    overflow: hidden;
    background: var(--paper);
  }
  .label__scene {
    position: absolute;
    inset: 0;
    background: linear-gradient(
      to bottom,
      var(--paper) 0%,
      var(--paper) 20%,
      var(--mist) 23%,
      var(--sky-wash) 26%,
      var(--wave-light) 30%,
      var(--wave) 36%,
      var(--wave-deep) 42%,
      var(--wave) 46%,
      var(--wave-light) 50%,
      var(--foam) 55%,
      var(--foam) 58%,
      var(--wet-sand) 63%,
      var(--foam) 69%,
      var(--sand) 72%,
      var(--sand-light) 84%,
      var(--sand) 100%
    );
  }
  .label__content {
    position: absolute;
    inset: 0;
    text-align: center;
  }
  .label__content > * { position: absolute; left: 0; right: 0; }
  .title { position: static; font-weight: 800; line-height: 1; }
  .title span { position: absolute; left: 0; right: 0; }
  .title__lead { top: 93px; font-size: 33px; }
  .title__word { font-size: 70px; letter-spacing: 0.005em; }
  .title__word--first { top: 141px; }
  .title__word--second { top: 224px; }
  .title__word--third { top: 306px; }
  .claim {
    top: 398px;
    font-size: 17px;
    font-weight: 400;
    line-height: 22.5px;
  }
  .treatment {
    top: 484px;
    font-size: 19px;
    font-weight: 600;
  }
  .weight {
    top: 518px;
    font-size: 24px;
    font-weight: 600;
  }
  .product-type {
    top: 561px;
    font-size: 17px;
    font-weight: 300;
  }
  .brand {
    top: 756px;
    font-size: 15px;
    font-weight: 800;
    letter-spacing: 0.28em;
  }
</style>
</head>
<body>
  <main class="label">
    <div class="label__scene" role="img" aria-label="Aerial view of a blue ocean wave breaking into white foam over a golden sandy beach"></div>
    <div class="label__content">
      <h1 class="title">
        <span class="title__lead">THE</span>
        <span class="title__word title__word--first">SURF</span>
        <span class="title__word title__word--second">SOOTHED</span>
        <span class="title__word title__word--third">SOAK</span>
      </h1>
      <p class="claim">bath soak to relieve symptoms<br>of mid eczema &amp; itchy, irritated,<br>dry skin</p>
      <p class="treatment">SOOTHING TREATMENT</p>
      <p class="weight">170g/60oz</p>
      <p class="product-type">BATH SOAK</p>
      <p class="brand">TIDEMARK</p>
    </div>
  </main>
</body>
</html>
```